I will ask the design of the business card

We are looking for business card design of the new company "R DOVE PAYGRID WORKS LLC." Based in Azerbaijan.
In case
We are working on Azerbaijan to set up the first exchange of crypto currencies.

The key currency used in exchanges is called "PLUME".
In case
We are doing project to make crypto currency infrastructure.

We provide state-of-the-art technology to the world.

```html
<!DOCTYPE html>
<html lang="en">
<head>
<meta charset="UTF-8">
<title>R Dove Paygrid Works LLC — Business Card</title>
<link rel="stylesheet" href="https://fonts.googleapis.com/css2?family=Oswald:wght@500&family=Work+Sans:wght@400;500&display=swap">
<style>
  :root {
    --backdrop: #1c1c1d;
    --card: #1f1f20;
    --card-edge: #262627;
    --accent: #1f72c4;
    --text-light: #f2f2f2;
    --text-muted: #d9d9d9;
  }
  * { box-sizing: border-box; margin: 0; padding: 0; }
  html, body {
    width: 1200px;
    height: 900px;
    overflow: hidden;
    background: var(--backdrop);
  }
  .stage {
    width: 1200px;
    height: 900px;
    display: flex;
    flex-direction: column;
    align-items: center;
    justify-content: center;
    gap: 44px;
  }
  .card {
    position: relative;
    width: 630px;
    height: 360px;
    background: linear-gradient(135deg, var(--card) 0%, var(--card-edge) 100%);
    box-shadow: 0 10px 30px rgba(0, 0, 0, 0.45);
    font-family: "Work Sans", sans-serif;
    color: var(--text-light);
  }
  .card__strip {
    position: absolute;
    left: 0;
    right: 0;
    bottom: 0;
    height: 7px;
    background: var(--accent);
  }

  /* Front */
  .card--front {
    display: flex;
    align-items: center;
    justify-content: center;
  }
  .brand {
    display: flex;
    align-items: center;
    gap: 14px;
    margin-bottom: 14px;
  }
  .brand__dot {
    width: 34px;
    height: 34px;
    border-radius: 50%;
    background: var(--accent);
  }
  .brand__name {
    font-weight: 500;
    font-size: 27px;
    letter-spacing: 1.5px;
    color: var(--text-light);
  }

  /* Back */
  .identity {
    position: absolute;
    top: 118px;
    left: 64px;
    display: flex;
    align-items: center;
  }
  .person {
    text-align: right;
    padding-right: 24px;
  }
  .person__name {
    font-family: "Oswald", sans-serif;
    font-weight: 500;
    font-size: 38px;
    letter-spacing: 1px;
    line-height: 1;
    text-transform: uppercase;
    color: var(--accent);
  }
  .person__role {
    margin-top: 6px;
    font-size: 17px;
    color: var(--text-muted);
  }
  .divider {
    width: 2px;
    height: 62px;
    background: var(--text-muted);
  }
  .contacts {
    list-style: none;
    padding-left: 24px;
    font-size: 17px;
    line-height: 1.35;
  }
  .contacts__item {
    display: flex;
    align-items: center;
    gap: 10px;
  }
  .contacts__icon {
    width: 11px;
    height: 11px;
    flex: none;
  }
  .contacts__link-host { color: var(--accent); }
  .address {
    position: absolute;
    left: 64px;
    bottom: 46px;
    font-size: 18px;
    letter-spacing: 0.3px;
    color: var(--text-light);
  }
</style>
</head>
<body>
<main class="stage">
  <section class="card card--front" aria-label="Card front">
    <div class="brand">
      <span class="brand__dot"></span>
      <span class="brand__name">R DOVE PAYGRID WORKS LLC.</span>
    </div>
    <div class="card__strip"></div>
  </section>

  <section class="card card--back" aria-label="Card back">
    <div class="identity">
      <div class="person">
        <p class="person__name">Daniel Reyes</p>
        <p class="person__role">Director</p>
      </div>
      <div class="divider"></div>
      <ul class="contacts">
        <li class="contacts__item">
          <svg class="contacts__icon" viewBox="0 0 24 24" aria-hidden="true"><path fill="#1f72c4" d="M6.6 10.8a15 15 0 0 0 6.6 6.6l2.2-2.2c.3-.3.7-.4 1-.2 1.1.4 2.3.6 3.6.6.6 0 1 .4 1 1V20c0 .6-.4 1-1 1A17 17 0 0 1 3 4c0-.6.4-1 1-1h3.5c.6 0 1 .4 1 1 0 1.3.2 2.5.6 3.6.1.3 0 .7-.2 1z"/></svg>
          <span>615-555-0142</span>
        </li>
        <li class="contacts__item">
          <svg class="contacts__icon" viewBox="0 0 24 24" aria-hidden="true"><rect x="2" y="5" width="20" height="14" rx="1.5" fill="none" stroke="#1f72c4" stroke-width="2.4"/><path d="M2.5 6l9.5 7 9.5-7" fill="none" stroke="#1f72c4" stroke-width="2.4"/></svg>
          <span>support@plume.technology</span>
        </li>
        <li class="contacts__item">
          <svg class="contacts__icon" viewBox="0 0 24 24" aria-hidden="true"><circle cx="12" cy="12" r="10" fill="none" stroke="#1f72c4" stroke-width="2.2"/><ellipse cx="12" cy="12" rx="4.5" ry="10" fill="none" stroke="#1f72c4" stroke-width="2"/><path d="M2 12h20" stroke="#1f72c4" stroke-width="2"/></svg>
          <span>www.<span class="contacts__link-host">ledger.plume.technology</span></span>
        </li>
      </ul>
    </div>
    <p class="address">AZ1010 , 8/3N. Sahil str. Baku city, Azerbaijan</p>
    <div class="card__strip"></div>
  </section>
</main>
</body>
</html>
```